Business card for a new cabinet shop company named Veloran Cabinets for high end cabinets

Design a business card, thinking dark rich green with colours to speak of high end luxury ie; cream, gold, black possibly

Mitchell Tarrowby
Director Craftsman
Email: info@veloranjoinery-example.com.au
Instagram : @veloran.cabinets

```html
<!DOCTYPE html>
<html lang="en">
<head>
<meta charset="utf-8">
<title>Veloran Cabinets – Business Card</title>
<link rel="stylesheet" href="https://fonts.googleapis.com/css2?family=Roboto:wght@400;500&display=swap">
<style>
  :root {
    --page: #f1f1f1;
    --card-dark: #222226;
    --emboss: #141416;
    --green: #0b9446;
    --gold: #c9ad6a;
    --white: #ffffff;
  }
  * { margin: 0; padding: 0; box-sizing: border-box; }
  html, body { width: 1200px; height: 990px; overflow: hidden; }
  body {
    background: var(--page);
    font-family: "Roboto", Arial, sans-serif;
    position: relative;
  }
  .card {
    position: absolute;
    left: 244px;
    width: 712px;
    height: 407px;
    border-radius: 32px;
    background: var(--green);
    overflow: hidden;
  }
  .card-front { top: 68px; }
  .card-back { top: 515px; }
  .card-face {
    position: absolute;
    left: 5px; top: 0; right: 0; bottom: 4px;
    border-radius: 30px;
    background: var(--card-dark);
  }
  .card-back .card-face { bottom: 0; }

  /* Front */
  .front-name {
    position: absolute;
    left: 0; right: 0; top: 120px;
    text-align: center;
    color: var(--emboss);
    font-weight: 500;
  }
  .front-name .word { display: block; font-size: 86px; line-height: 1; letter-spacing: 1px; }
  .front-name .sub { display: block; font-size: 40px; letter-spacing: 22px; margin-top: 14px; padding-left: 22px; }

  /* Back */
  .brand-name {
    position: absolute;
    left: 34px; top: 28px;
    color: var(--gold);
    font-weight: 400;
  }
  .brand-name .word { display: block; font-size: 46px; line-height: 1; }
  .brand-name .sub { display: block; font-size: 24px; letter-spacing: 9px; margin-top: 12px; }

  .holder {
    position: absolute;
    right: 31px; top: 36px;
    text-align: right;
  }
  .holder-name { font-size: 40px; line-height: 1; letter-spacing: 0.5px; }
  .holder-name .first { color: var(--gold); font-weight: 500; }
  .holder-name .last { color: var(--green); font-weight: 400; }
  .holder-title { color: var(--white); font-size: 17px; margin-top: 8px; letter-spacing: 0.6px; }
  .gold-tab {
    position: absolute;
    right: 0; top: 35px;
    width: 23px; height: 66px;
    background: var(--gold);
  }

  .contacts {
    position: absolute;
    left: 22px; top: 240px;
    list-style: none;
  }
  .contacts li {
    display: flex; align-items: center;
    height: 24px;
    color: var(--white);
    font-size: 18px;
    letter-spacing: 0.4px;
  }
  .contacts svg { width: 16px; height: 16px; margin-right: 11px; flex: none; }

  .wave { position: absolute; left: 0; top: 0; width: 712px; height: 407px; }
</style>
</head>
<body>

<section class="card card-front" aria-label="Card front">
  <div class="card-face">
    <div class="front-name">
      <span class="word">Veloran</span>
      <span class="sub">CABINETS</span>
    </div>
  </div>
</section>

<section class="card card-back" aria-label="Card back">
  <div class="card-face">
    <svg class="wave" viewBox="0 0 712 407" aria-hidden="true">
      <path d="M0 351 C60 385 120 392 180 391 C300 388 400 330 497 277 C580 232 650 250 712 274 L712 407 L0 407 Z" fill="var(--green)"/>
      <path d="M0 317 C70 370 170 386 269 377 C180 383 80 372 0 336 Z" fill="var(--gold)"/>
    </svg>

    <div class="brand-name">
      <span class="word">Veloran</span>
      <span class="sub">CABINETS</span>
    </div>

    <div class="holder">
      <p class="holder-name"><span class="first">Mitchell</span> <span class="last">Tarrowby</span></p>
      <p class="holder-title">Director Craftsman</p>
    </div>
    <div class="gold-tab"></div>

    <ul class="contacts">
      <li>
        <svg viewBox="0 0 16 16" aria-hidden="true"><rect x="1.5" y="1.5" width="13" height="13" rx="3" fill="none" stroke="var(--gold)" stroke-width="1.6"/></svg>
        @veloran.cabinets
      </li>
      <li>
        <svg viewBox="0 0 16 16" aria-hidden="true"><rect x="1" y="4" width="14" height="10" fill="none" stroke="var(--gold)" stroke-width="1.5"/><path d="M1 4 L8 10 L15 4" fill="none" stroke="var(--gold)" stroke-width="1.5"/></svg>
        info@veloranjoinery-example.com.au
      </li>
      <li>
        <svg viewBox="0 0 16 16" aria-hidden="true"><circle cx="8" cy="8" r="6.5" fill="none" stroke="var(--gold)" stroke-width="1.5"/><ellipse cx="8" cy="8" rx="2.8" ry="6.5" fill="none" stroke="var(--gold)" stroke-width="1.2"/><path d="M1.5 8 H14.5" stroke="var(--gold)" stroke-width="1.2"/></svg>
        www.veloranjoinery-example.com.au
      </li>
    </ul>
  </div>
</section>

</body>
</html>
```